Year End Gift for Employees

Looking for assistance in creating an album cover. Here are some ideas that I have: Double Platinum, Lantern Crow Drifting, 2025 World Tour
QT/QR (name of the band) – on the front of the album cover
List of Songs - on the back of the album cover
Would like to have the ability to have team / individual pictures on the inside of the double platinum album cover
DON’T want anything gory or vulgar for the album cover
Also want rights to the image for the album cover to use for t-shirts
This is a Sales Team that work within Home Improvement Industries
Any additional images that you want to propose, I'm open too. Thanks and I'll await your response
Colleagues

```html
<!DOCTYPE html>
<html lang="en">
<head>
<meta charset="utf-8">
<title>QT/QR 2025 World Tour – Album and Shirt Set</title>
<link rel="stylesheet" href="https://fonts.googleapis.com/css2?family=Anton&family=Oswald:wght@300;400&family=Sacramento&family=Pirata+One&display=swap">
<style>
  :root {
    --backdrop: #8a8a8a;
    --silver-light: #eef1f5;
    --silver-mid: #c3ccd8;
    --silver-dark: #97a3b3;
    --metal-ink: #7f8c9d;
    --ink: #1a1a1a;
    --title-red: #d21f17;
    --shirt: #0c0c0c;
    --print-silver: #a9b8cc;
    --print-light: #dfe6ef;
  }
  * { margin: 0; padding: 0; box-sizing: border-box; }
  html, body { width: 1200px; height: 541px; overflow: hidden; }
  body { background: var(--backdrop); position: relative; font-family: "Oswald", sans-serif; }

  .metal {
    background: linear-gradient(135deg, var(--silver-mid) 0%, var(--silver-light) 30%, var(--silver-dark) 55%, var(--silver-light) 78%, var(--silver-mid) 100%);
  }
  .band-name {
    font-family: "Anton", sans-serif;
    color: var(--metal-ink);
    text-align: center;
    line-height: 1;
    letter-spacing: 2px;
  }
  .tour-script {
    font-family: "Sacramento", cursive;
    color: var(--ink);
    text-align: center;
    line-height: 1;
  }

  /* Front cover */
  .front-cover { position: absolute; left: 26px; top: 28px; width: 230px; height: 230px; }
  .front-cover .band-name { position: absolute; left: 0; width: 100%; font-size: 78px; }
  .front-cover .band-name.upper { top: 14px; }
  .front-cover .band-name.lower { top: 128px; }
  .front-cover .tour-script { position: absolute; left: 0; width: 100%; top: 102px; font-size: 24px; }

  /* Back cover */
  .back-cover { position: absolute; left: 280px; top: 28px; width: 230px; height: 230px; }
  .back-cover .album-title {
    position: absolute; top: 8px; left: 0; width: 100%; text-align: center;
    font-family: "Anton", sans-serif; color: var(--title-red); font-size: 19px; line-height: 1;
  }
  .back-cover .tour-script { position: absolute; top: 30px; left: 0; width: 100%; font-size: 16px; }
  .track-list {
    position: absolute; list-style: none; font-weight: 300; font-size: 10px;
    line-height: 14.7px; color: var(--ink); text-align: center; width: 110px;
  }
  .track-list.side-a { left: 8px; top: 62px; }
  .track-list.side-b { left: 110px; top: 68px; }

  /* Disc */
  .disc { position: absolute; left: 144px; top: 284px; width: 228px; height: 228px; border-radius: 50%; overflow: hidden; }
  .disc .band-name { position: absolute; left: 0; width: 100%; font-size: 72px; }
  .disc .band-name.upper { top: 16px; }
  .disc .band-name.lower { top: 118px; }
  .disc .tour-script { position: absolute; left: 132px; top: 102px; width: 90px; font-size: 17px; }
  .disc-hole { position: absolute; left: 96px; top: 96px; width: 36px; height: 36px; border-radius: 50%; background: var(--backdrop); }

  /* Shirt prints */
  .shirt-front { position: absolute; left: 566px; top: 40px; width: 258px; height: 330px; background: var(--shirt); border-radius: 6px; }
  .shirt-front .band-name { position: absolute; left: 0; width: 100%; font-size: 68px; color: var(--print-silver); }
  .shirt-front .band-name.upper { top: 70px; }
  .shirt-front .band-name.lower { top: 150px; }
  .shirt-front .tour-script { position: absolute; left: 0; width: 100%; top: 137px; font-size: 20px; color: var(--print-light); }

  .shirt-back { position: absolute; left: 880px; top: 170px; width: 230px; height: 330px; background: var(--shirt); border-radius: 6px; }
  .tour-dates {
    position: absolute; top: 68px; left: 0; width: 100%; list-style: none; text-align: center;
    font-family: "Pirata One", serif; font-size: 8px; line-height: 17px; color: var(--print-silver);
  }
</style>
</head>
<body>

<section class="front-cover metal" aria-label="Album front cover">
  <div class="band-name upper">QT/QR</div>
  <div class="tour-script">2025 World Tour</div>
  <div class="band-name lower">QT/QR</div>
</section>

<section class="back-cover metal" aria-label="Album back cover">
  <h1 class="album-title">LANTERN CROW DRIFTING</h1>
  <div class="tour-script">2025 World Tour</div>
  <ol class="track-list side-a">
    <li>1. Song Name</li>
    <li>2. Another Song Name</li>
    <li>3. Song Name</li>
    <li>4. Even Longer Song Name</li>
    <li>5. Song Name</li>
    <li>6. Just a Song Name</li>
    <li>7. One More Song Name</li>
    <li>8. Song Name</li>
    <li>9. Song Name</li>
  </ol>
  <ol class="track-list side-b">
    <li>10. Song</li>
    <li>11. Maybe Song Name</li>
    <li>12. Pretty Song Name</li>
    <li>13. Another Name</li>
    <li>14. Song Name</li>
    <li>15. Yet anotherSong Name</li>
    <li>16. Song Name</li>
    <li>17. Last Name</li>
  </ol>
</section>

<section class="disc metal" aria-label="Disc label">
  <div class="band-name upper">QT/QR</div>
  <div class="band-name lower">QT/QR</div>
  <div class="tour-script">2025 World Tour</div>
  <div class="disc-hole"></div>
</section>

<section class="shirt-front" aria-label="T-shirt front print">
  <div class="band-name upper">QT/QR</div>
  <div class="tour-script">2025 World Tour</div>
  <div class="band-name lower">QT/QR</div>
</section>

<section class="shirt-back" aria-label="T-shirt back print">
  <ul class="tour-dates">
    <li>Feb 12, 2025 – Seattle, WA</li>
    <li>Mar 03, 2025 – Denver, CO</li>
    <li>Mar 28, 2025 – Austin, TX</li>
    <li>Apr 10, 2025 – New Orleans, LA</li>
    <li>May 02, 2025 – Nashville, TN</li>
    <li>Jun 14, 2025 – Chicago, IL</li>
    <li>Jul 09, 2025 – Toronto, ON</li>
    <li>Aug 21, 2025 – New York, NY</li>
    <li>Sep 18, 2025 – Boston, MA</li>
    <li>Oct 30, 2025 – Los Angeles, CA</li>
  </ul>
</section>

</body>
</html>
```